Business card design for Brivo Engineering Tandem

We need a new business card design along with all the necessary to place an order. The company is Brivo Engineering Tandem and we recently updated our logo.

```html
<!DOCTYPE html>
<html lang="en">
<head>
<meta charset="utf-8">
<title>Brivo Engineering Tandem – Business Card</title>
<link href="https://fonts.googleapis.com/css2?family=Kanit:wght@400;500;600&display=swap" rel="stylesheet">
<style>
  :root {
    --backdrop: #3b3b3c;
    --card: #ffffff;
    --brand-yellow: #e0bc22;
    --brand-grey: #939393;
    --ink: #1f1f1f;
  }
  * { margin: 0; padding: 0; box-sizing: border-box; }
  html, body {
    width: 1200px;
    height: 1059px;
    overflow: hidden;
    background: var(--backdrop);
    font-family: "Kanit", sans-serif;
  }
  .canvas { position: relative; width: 1200px; height: 1059px; }

  .card {
    position: absolute;
    background: var(--card);
    border-radius: 24px;
  }
  .card--front { left: 256px; top: 100px; width: 688px; height: 393px; }
  .card--back  { left: 253px; top: 536px; width: 694px; height: 396px; }

  .wordmark {
    position: absolute;
    left: 0; right: 0;
    display: flex;
    align-items: center;
    justify-content: center;
    gap: 14px;
  }
  .wordmark__mark {
    background: var(--brand-yellow);
    flex: none;
  }
  .wordmark__name {
    color: var(--brand-grey);
    font-weight: 600;
    letter-spacing: 0.02em;
    text-transform: uppercase;
    white-space: nowrap;
  }
  .card--front .wordmark { top: 162px; transform: translateY(-50%); }
  .card--front .wordmark__mark { width: 30px; height: 30px; }
  .card--front .wordmark__name { font-size: 32px; }
  .card--back .wordmark { top: 198px; transform: translateY(-50%); }
  .card--back .wordmark__mark { width: 34px; height: 34px; }
  .card--back .wordmark__name { font-size: 36px; }
  .card--front .wordmark { top: 87px; }

  .person {
    position: absolute;
    right: calc(688px - 301px);
    top: 215px;
    text-align: right;
  }
  .person__name {
    color: var(--brand-yellow);
    font-weight: 600;
    font-size: 31px;
    line-height: 1;
    letter-spacing: -0.01em;
  }
  .person__role {
    color: var(--ink);
    font-size: 17px;
    margin-top: 9px;
  }

  .divider {
    position: absolute;
    left: 329px;
    top: 216px;
    width: 2px;
    height: 70px;
    background: var(--brand-yellow);
  }

  .contacts {
    position: absolute;
    left: 357px;
    top: 208px;
    list-style: none;
  }
  .contacts li {
    display: flex;
    align-items: center;
    gap: 8px;
    height: 27px;
    color: var(--ink);
    font-size: 17.5px;
  }
  .contacts svg { width: 14px; height: 14px; flex: none; fill: var(--brand-yellow); }

  .address {
    position: absolute;
    left: 0; right: 0;
    top: 338px;
    text-align: center;
    color: var(--ink);
    font-size: 17px;
  }
</style>
</head>
<body>
<div class="canvas">

  <section class="card card--front" aria-label="Business card front">
    <div class="wordmark">
      <span class="wordmark__mark" aria-hidden="true"></span>
      <span class="wordmark__name">Brivo Engineering Tandem</span>
    </div>

    <div class="person">
      <p class="person__name">DANIEL HART</p>
      <p class="person__role">Managing Director</p>
    </div>

    <span class="divider" aria-hidden="true"></span>

    <ul class="contacts">
      <li>
        <svg viewBox="0 0 24 24" aria-hidden="true"><path d="M6.6 10.8a15.1 15.1 0 0 0 6.6 6.6l2.2-2.2a1 1 0 0 1 1-.25 11.4 11.4 0 0 0 3.6.57 1 1 0 0 1 1 1V20a1 1 0 0 1-1 1A17 17 0 0 1 3 4a1 1 0 0 1 1-1h3.5a1 1 0 0 1 1 1c0 1.25.2 2.45.57 3.57a1 1 0 0 1-.25 1z"/></svg>
        01632 960482
      </li>
      <li>
        <svg viewBox="0 0 24 24" aria-hidden="true"><path d="M2 5h20v14H2z M2 5l10 7 10-7" fill="var(--brand-yellow)"/><path d="M2 6l10 7 10-7" fill="none" stroke="#fff" stroke-width="1.6"/></svg>
        sales@brivoengineering.co.uk
      </li>
      <li>
        <svg viewBox="0 0 24 24" aria-hidden="true"><circle cx="12" cy="12" r="10"/><path d="M2 12h20M12 2c3 3 3 17 0 20M12 2c-3 3-3 17 0 20" fill="none" stroke="#fff" stroke-width="1.4"/></svg>
        www.brivoengineering.co.uk
      </li>
    </ul>

    <p class="address">Brivo Engineering Tandem 24b Harlow Road, Kettering NN15 6TR</p>
  </section>

  <section class="card card--back" aria-label="Business card back">
    <div class="wordmark">
      <span class="wordmark__mark" aria-hidden="true"></span>
      <span class="wordmark__name">Brivo Engineering Tandem</span>
    </div>
  </section>

</div>
</body>
</html>
```